Vantrel System Web Page Design

This project is to design 6 pages of a web based medical system for clinics, hospitals, drugs suppliers, general items suppliers, insurance company, laboratories and patients (basically all parties which could be involved in).We want the designs of the browser, button, icon and layout are based on Zeltor, which is user friendly, looks professional, simple and neat but with powerful functions. We have uploaded few pictures of another system, please do not copy its design because this is not what we are looking for, the pictures are for you to know the elements should be included in our pages. Vantrel web-base system, design 6 pages1. Login PageShould include the following elements-company id with input field-login id with input field-password with input field2. Main Page (Navigation page)Should include the following elements-Appointment-Consultation-Patient-Drugs inventory -General supplies inventory -Laboratory-Suppliers-Insurance-Reports 3. Appointment PageShould include all the the elements in the respective pictures plus the followings-Daily View, Weekly View, Monthly View buttons4. Consultation PageShould include all the the elements in the respective picture5. Patient Page5.1 General information Should include all the the elements in the respective picture5.2 medical history/lab reportsShould include all the the elements in the respective picture plus the followings-Notify patient button-Share report button.
Updated on 28 Nov:
Please stop using Harbor Suite in your designs which is not the name of our system. We have just rename our system to Vantrel, please take note.
We need the system to look professional not playful, do not use too many colors and playful icons.

```html
<!DOCTYPE html>
<html lang="en">
<head>
<meta charset="utf-8">
<title>Vantrel – Clinic System Screens</title>
<link href="https://fonts.googleapis.com/css2?family=Poppins:wght@400;500;600;700&display=swap" rel="stylesheet">
<style>
:root{
  --stage:#7b7b7b;
  --navy:#2b23a8;
  --navy-dark:#1f1a86;
  --cream:#fdf8dc;
  --panel:#eeeef2;
  --card:#ffffff;
  --line:#d9d9e3;
  --ink:#2a2a3a;
  --muted:#8a8aa0;
  --accent:#d6263b;
}
*{box-sizing:border-box;margin:0;padding:0}
html,body{width:1200px;height:2368px;overflow:hidden}
body{background:var(--stage);font-family:'Poppins',sans-serif;color:var(--ink);position:relative}
.screen{position:absolute;left:88px;width:1064px;overflow:hidden;background:var(--panel)}

/* login */
.login{top:8px;height:652px;display:flex}
.login-hero{width:512px;height:100%;background:linear-gradient(160deg,#4b46c9,#2b23a8 60%,#3a34b6);position:relative}
.hero-brand{position:absolute;left:40px;bottom:110px;color:#fff;font-weight:700;font-size:30px;display:flex;align-items:center;gap:10px}
.brand-square{width:22px;height:22px;background:var(--accent)}
.login-side{flex:1;background:var(--cream);position:relative}
.login-brand{position:absolute;left:60px;top:140px;width:432px;text-align:center}
.login-brand .name{font-weight:700;font-size:34px;color:var(--navy);display:inline-flex;align-items:center;gap:10px}
.login-brand .edition{font-size:14px;color:var(--accent);font-weight:600;text-align:right;padding-right:60px}
.login-form{position:absolute;left:92px;top:250px;width:372px}
.field{height:40px;background:#fff;border:1px solid var(--line);border-radius:3px;display:flex;align-items:center;gap:10px;padding:0 12px;font-size:13px;color:var(--muted);margin-bottom:20px}
.submit{height:48px;background:var(--navy);color:#fff;font-weight:600;font-size:16px;display:flex;align-items:center;justify-content:center;border-radius:3px;margin-top:6px}
.login-extra{display:flex;justify-content:space-between;font-size:11px;color:var(--muted);margin-top:10px}
.login-extra span:first-child::before{content:"";display:inline-block;width:10px;height:10px;border:1px solid var(--muted);margin-right:6px;vertical-align:-1px}

/* shell */
.sidebar{position:absolute;left:0;top:0;width:252px;height:100%;background:var(--navy);color:#fff}
.avatar{position:absolute;left:66px;top:20px;width:118px;height:118px;border-radius:50%;background:radial-gradient(circle at 50% 40%,#c9c2ba,#7d8791);border:4px solid #fff}
.user{position:absolute;top:150px;width:100%;text-align:center}
.user .nm{font-size:18px;font-weight:600}
.user .role{font-size:12px;opacity:.8}
.hotline{position:absolute;left:22px;bottom:34px;display:flex;align-items:center;gap:10px}
.hotline .lbl{font-size:12px}
.hotline .num{font-size:20px;font-weight:600}
.copy{position:absolute;left:12px;bottom:8px;font-size:8px;opacity:.7}
.topbar{position:absolute;left:252px;top:0;right:0;height:56px;background:#fff;display:flex;align-items:center;padding:0 30px;gap:26px;font-size:13px}
.search{width:330px;height:32px;border:1px solid var(--line);border-radius:16px;display:flex;align-items:center;gap:8px;padding:0 14px;color:var(--muted);margin-right:auto}
.lang{display:flex;align-items:center;gap:6px}

/* main menu */
.menu{top:700px;height:680px}
.tile{position:absolute;width:224px;height:176px;background:var(--card);box-shadow:0 2px 6px rgba(0,0,0,.08);text-align:center;padding-top:24px}
.tile h3{font-size:16px;font-weight:600;color:var(--navy);line-height:1.15}
.tile svg{margin-top:14px}

/* records */
.records{top:1448px;height:880px}
.tab{position:absolute;left:282px;top:70px;padding:4px 16px;background:#fff;font-size:12px;border:1px solid var(--line);border-bottom:none}
.gallery{position:absolute;left:270px;top:94px;width:774px;height:510px;background:#fff;border:1px solid var(--line)}
.item{position:absolute;width:172px}
.thumb{height:150px;width:100%}
.cap{height:24px;background:var(--navy);color:#fff;font-size:11px;display:flex;align-items:center;justify-content:center;white-space:nowrap}
.date{display:flex;align-items:center;justify-content:center;gap:8px;font-size:11px;margin-top:8px;color:var(--ink)}
.date i{width:12px;height:12px;background:var(--navy);display:inline-block;border-radius:2px}
.btn{position:absolute;height:24px;width:110px;background:var(--navy);color:#fff;font-size:11px;display:flex;align-items:center;justify-content:center;border-radius:2px;white-space:nowrap}
.preview{position:absolute;left:290px;top:780px;width:90px;height:76px;background:#000}
</style>
</head>
<body>

<!-- Login -->
<section class="screen login">
  <div class="login-hero" role="img" aria-label="Photo of a smiling medical team under a blue tint">
    <div class="hero-brand"><span class="brand-square"></span>Vantrel</div>
  </div>
  <div class="login-side">
    <div class="login-brand">
      <div class="name"><span class="brand-square"></span>Vantrel</div>
      <div class="edition">Professional Edition</div>
    </div>
    <form class="login-form">
      <div class="field"><svg width="14" height="14" viewBox="0 0 14 14"><rect x="2" y="1" width="10" height="12" fill="none" stroke="#8a8aa0"/></svg>Company ID</div>
      <div class="field"><svg width="14" height="14" viewBox="0 0 14 14"><circle cx="7" cy="5" r="3" fill="none" stroke="#8a8aa0"/><path d="M2 13c1-3 9-3 10 0" fill="none" stroke="#8a8aa0"/></svg>Login ID</div>
      <div class="field"><svg width="14" height="14" viewBox="0 0 14 14"><rect x="2" y="6" width="10" height="7" fill="none" stroke="#8a8aa0"/><path d="M4 6V4a3 3 0 0 1 6 0v2" fill="none" stroke="#8a8aa0"/></svg>Password</div>
      <div class="submit">Submit</div>
      <div class="login-extra"><span>Remember me</span><span>Forgot Password?</span></div>
    </form>
  </div>
</section>

<!-- Main menu -->
<section class="screen menu">
  <aside class="sidebar">
    <div class="avatar" role="img" aria-label="Profile photo of the signed-in doctor"></div>
    <div class="user"><div class="nm">John Doe</div><div class="role">General Surgeon</div></div>
    <div class="hotline"><svg width="28" height="28" viewBox="0 0 24 24"><path d="M5 3h4l2 5-3 2a11 11 0 0 0 6 6l2-3 5 2v4a2 2 0 0 1-2 2A17 17 0 0 1 3 5a2 2 0 0 1 2-2z" fill="none" stroke="#fff" stroke-width="1.6"/></svg><div><div class="lbl">Support Hotline</div><div class="num">852 2000 0100</div></div></div>
    <div class="copy">© 2018 Northway Medical Solution Limited</div>
  </aside>
  <header class="topbar">
    <div class="search">&#9906; Search</div><span>About Us</span><span>Our Process</span><span class="lang">English ▾</span>
  </header>

  <div class="tile" style="left:292px;top:80px"><h3>Appointment</h3><svg width="70" height="70" viewBox="0 0 70 70" fill="none" stroke="#2b23a8" stroke-width="3"><rect x="8" y="12" width="54" height="48" rx="3"/><path d="M8 24h54M20 6v12M50 6v12"/><path d="M18 34h8M31 34h8M44 34h8M18 46h8M31 46h8"/></svg></div>
  <div class="tile" style="left:546px;top:80px"><h3>Consultation</h3><svg width="70" height="70" viewBox="0 0 70 70" fill="none" stroke="#2b23a8" stroke-width="3"><rect x="12" y="10" width="46" height="52" rx="3"/><rect x="24" y="5" width="22" height="10" rx="2"/><path d="M35 26v16M27 34h16M20 52h30"/></svg></div>
  <div class="tile" style="left:800px;top:80px"><h3>Patient</h3><svg width="70" height="70" viewBox="0 0 70 70" fill="none" stroke="#2b23a8" stroke-width="3"><circle cx="35" cy="22" r="12"/><path d="M12 64c2-16 44-16 46 0"/><path d="M35 44v12"/></svg></div>

  <div class="tile" style="left:292px;top:280px"><h3>Drugs inventory</h3><svg width="70" height="70" viewBox="0 0 70 70" fill="none" stroke="#2b23a8" stroke-width="3"><rect x="18" y="20" width="34" height="44" rx="4"/><rect x="22" y="8" width="26" height="12"/><path d="M35 32v20M25 42h20"/></svg></div>
  <div class="tile" style="left:546px;top:280px"><h3>General supplies<br>inventory</h3><svg width="70" height="60" viewBox="0 0 70 60" fill="none" stroke="#2b23a8" stroke-width="3"><rect x="8" y="8" width="40" height="44"/><path d="M8 22h40"/><circle cx="46" cy="38" r="11"/><path d="M54 46l10 10"/></svg></div>
  <div class="tile" style="left:800px;top:280px"><h3>Laboratory</h3><svg width="70" height="70" viewBox="0 0 70 70" fill="none" stroke="#2b23a8" stroke-width="3"><path d="M27 8h16M30 8v20L14 60h42L40 28V8"/><path d="M21 46h28"/></svg></div>

  <div class="tile" style="left:292px;top:480px"><h3>Suppliers</h3><svg width="70" height="70" viewBox="0 0 70 70" fill="none" stroke="#2b23a8" stroke-width="3"><path d="M6 12h10l8 34h32l6-24H20"/><circle cx="28" cy="56" r="5"/><circle cx="52" cy="56" r="5"/></svg></div>
  <div class="tile" style="left:546px;top:480px"><h3>Insurance</h3><svg width="70" height="70" viewBox="0 0 70 70" fill="none" stroke="#2b23a8" stroke-width="3"><path d="M35 6l24 9v18c0 15-10 25-24 31C21 58 11 48 11 33V15z"/><path d="M35 24v18M26 33h18"/></svg></div>
  <div class="tile" style="left:800px;top:480px"><h3>Reports</h3><svg width="70" height="70" viewBox="0 0 70 70" fill="none" stroke="#2b23a8" stroke-width="3"><rect x="14" y="6" width="42" height="56" rx="3"/><path d="M22 20h26M22 30h26M22 40h16"/><path d="M22 52l8-6 6 4 12-10"/></svg></div>
</section>

<!-- Medical history / lab reports -->
<section class="screen records">
  <aside class="sidebar">
    <div class="avatar" role="img" aria-label="Profile photo of the signed-in doctor"></div>
    <div class="user"><div class="nm">John Doe</div><div class="role">General Surgeon</div></div>
    <div class="hotline"><svg width="28" height="28" viewBox="0 0 24 24"><path d="M5 3h4l2 5-3 2a11 11 0 0 0 6 6l2-3 5 2v4a2 2 0 0 1-2 2A17 17 0 0 1 3 5a2 2 0 0 1 2-2z" fill="none" stroke="#fff" stroke-width="1.6"/></svg><div><div class="lbl">Support Hotline</div><div class="num">852 2000 0100</div></div></div>
    <div class="copy">© 2018 Northway Medical Solution Limited</div>
  </aside>
  <header class="topbar">
    <div class="search">&#9906; Search</div><span>About Us</span><span>Our Process</span><span class="lang">English ▾</span>
  </header>

  <div class="tab">Others</div>
  <div class="gallery">
    <div class="item" style="left:18px;top:18px"><div class="thumb" role="img" aria-label="Photo of printed medical records" style="background:linear-gradient(135deg,#c9d3de,#7f93aa)"></div><div class="cap">Medical Record Printing</div><div class="date"><i></i>25 / 12 / 2018<i></i></div></div>
    <div class="item" style="left:208px;top:18px"><div class="thumb" role="img" aria-label="Photo of a pulmonary CT scan" style="background:linear-gradient(135deg,#9fc3e6,#3a6fb0)"></div><div class="cap">Pulmonary CT</div><div class="date"><i></i>25 / 12 / 2018<i></i></div></div>
    <div class="item" style="left:398px;top:18px"><div class="thumb" role="img" aria-label="Image of a knee joint scan" style="background:linear-gradient(135deg,#2a4aa8,#c2452f)"></div><div class="cap">Knee</div><div class="date"><i></i>25 / 12 / 2018<i></i></div></div>
    <div class="item" style="left:588px;top:18px"><div class="thumb" role="img" aria-label="X-ray image of a hand" style="background:linear-gradient(135deg,#1a3d8c,#7fb4ea)"></div><div class="cap">X-ray Hand</div><div class="date"><i></i>25 / 12 / 2018<i></i></div></div>

    <div class="item" style="left:18px;top:256px"><div class="thumb" role="img" aria-label="X-ray image of a pelvis" style="background:linear-gradient(135deg,#2b2b2b,#9a9a9a)"></div><div class="cap">X-ray Pelvis</div><div class="date"><i></i>25 / 12 / 2018<i></i></div></div>
    <div class="item" style="left:208px;top:256px"><div class="thumb" role="img" aria-label="X-ray image of a chest" style="background:linear-gradient(135deg,#111,#8c8c8c)"></div><div class="cap">X-ray Chest</div><div class="date"><i></i>25 / 12 / 2018<i></i></div></div>
    <div class="item" style="left:398px;top:256px"><div class="thumb" role="img" aria-label="ECG trace on a blue screen" style="background:linear-gradient(135deg,#1f4fa3,#4f9be0)"></div><div class="cap">ECG</div><div class="date"><i></i>25 / 12 / 2018<i></i></div></div>
    <div class="item" style="left:588px;top:256px"><div class="thumb" role="img" aria-label="Photo of a printed patient report" style="background:linear-gradient(135deg,#e8ecf2,#9aa6b6)"></div><div class="cap">Patient Report</div><div class="date"><i></i>25 / 12 / 2018<i></i></div></div>
  </div>

  <div class="btn" style="left:290px;top:620px">Scan</div>
  <div class="btn" style="left:290px;top:650px">Delete</div>
  <div class="btn" style="left:290px;top:680px">&lt; Previous</div>
  <div class="btn" style="left:602px;top:620px">Print</div>
  <div class="btn" style="left:602px;top:650px">Remove</div>
  <div class="btn" style="left:602px;top:680px">Next &gt;</div>
  <div class="btn" style="left:914px;top:620px">Import</div>
  <div class="btn" style="left:914px;top:650px">Export</div>

  <div class="preview" role="img" aria-label="Selected image preview"></div>
  <div class="btn" style="left:780px;top:786px">Notify Patient</div>
  <div class="btn" style="left:780px;top:820px">Share Report</div>
  <div class="btn" style="left:914px;top:786px">Compare</div>
  <div class="btn" style="left:914px;top:820px">Return</div>
</section>

</body>
</html>
```